FunBrixo Business Card

We need a business card design for our company. We sell construction-themed amusement rides for kids.

Contact Information for Business Card

Contact info on business card should include:
Carl Dunning
Co-Founder & COO
(833) 571-FUNBRIX
Carl@funbrixo-demo.com
www.funbrixo-demo.com

```html
<!DOCTYPE html>
<html lang="en">
<head>
<meta charset="utf-8">
<title>FunBrixo Business Card</title>
<link href="https://fonts.googleapis.com/css2?family=Arimo:wght@400;700&display=swap" rel="stylesheet">
<style>
  :root {
    --backdrop: #2e2e30;
    --card: #232224;
    --accent: #f05a22;
    --text-light: #e6e6e6;
    --divider: #4a4a4c;
  }
  * { box-sizing: border-box; margin: 0; padding: 0; }
  html, body {
    width: 1200px; height: 900px; overflow: hidden;
    background: var(--backdrop);
    font-family: "Arimo", Arial, sans-serif;
  }
  .canvas { position: relative; width: 1200px; height: 900px; }
  .card {
    position: absolute; left: 300px; width: 600px; height: 340px;
    background: var(--card);
    border-bottom: 9px solid var(--accent);
    box-shadow: 0 6px 18px rgba(0,0,0,0.45);
  }
  .card-front { top: 80px; }
  .card-back { top: 480px; }
  .brand-name {
    position: absolute; color: var(--accent); font-weight: 700;
    letter-spacing: 0.5px; white-space: nowrap;
  }
  .card-front .brand-name {
    top: 50%; left: 50%; transform: translate(-50%, -50%); font-size: 64px;
  }
  .card-back .brand-name {
    top: 50%; left: 40px; transform: translateY(-50%); font-size: 44px;
  }
  .divider {
    position: absolute; left: 285px; top: 95px; width: 1px; height: 150px;
    background: var(--divider);
  }
  .contact-block { position: absolute; left: 312px; top: 98px; color: var(--text-light); }
  .person-name {
    color: var(--accent); font-weight: 700; font-size: 22px; letter-spacing: 0.5px;
  }
  .person-role { font-size: 17px; margin-top: 4px; margin-bottom: 12px; }
  .contact-list { list-style: none; }
  .contact-list li {
    display: flex; align-items: center; gap: 8px; font-size: 16px; line-height: 25px;
  }
  .contact-list svg { width: 16px; height: 16px; flex: none; }
</style>
</head>
<body>
<main class="canvas">
  <section class="card card-front">
    <div class="brand-name">FunBrixo</div>
  </section>

  <section class="card card-back">
    <div class="brand-name">FunBrixo</div>
    <div class="divider"></div>
    <div class="contact-block">
      <div class="person-name">CARL DUNNING</div>
      <div class="person-role">Co-Founder &amp; COO</div>
      <ul class="contact-list">
        <li>
          <svg viewBox="0 0 16 16" aria-hidden="true"><rect x="1" y="1" width="14" height="14" rx="2" fill="none" stroke="var(--accent)" stroke-width="1.5"/><path d="M5.5 4.5l1.5 1.5-1 1c.6 1.2 1.5 2.1 2.7 2.7l1-1 1.5 1.5-1 1.3C7.5 11 5 8.5 4.5 5.5z" fill="var(--accent)"/></svg>
          (833) 571-FUNBRIX
        </li>
        <li>
          <svg viewBox="0 0 16 16" aria-hidden="true"><rect x="1" y="3" width="14" height="10" fill="var(--accent)"/><path d="M1 3l7 6 7-6" fill="none" stroke="var(--card)" stroke-width="1.3"/></svg>
          Carl@funbrixo-demo.com
        </li>
        <li>
          <svg viewBox="0 0 16 16" aria-hidden="true"><circle cx="8" cy="8" r="7" fill="var(--accent)"/><g fill="none" stroke="var(--card)" stroke-width="1"><ellipse cx="8" cy="8" rx="3" ry="7"/><path d="M1 8h14M2.5 4.5h11M2.5 11.5h11"/></g></svg>
          www.funbrixo-demo.com
        </li>
      </ul>
    </div>
  </section>
</main>
</body>
</html>
```